Store Front Sign for Vape Store

Interested in getting a store front sign graphic done. Sign is for over the door (lighted sign). Dimensions of sign: 6 feet long x 2 feet high.
Sign is for a Vape Store. I have attached the logo to be used.
Looking for a modern and professional look
Phone numbers to be used.
Whatsapp# 394-6150
Contact #562-7038
Sign should have Instagram & Facebook logos and. handle @lumoramists

Industry/Entity Type

Vape | Electronic Cigarettes

Colors

Designer to choose colors to be used in the design.

Requirements
Must have
• Facebook and Instagram Logos. Contact Numbers.
Should not have
• Any Persons.

```html
<!DOCTYPE html>
<html lang="en">
<head>
<meta charset="utf-8">
<title>Lumora Mists – Vape Shop Sign</title>
<link rel="stylesheet" href="https://fonts.googleapis.com/css2?family=Montserrat:wght@600;700&family=Hind:wght@600&family=Poppins:wght@400&display=swap">
<style>
  :root {
    --page: #ffffff;
    --band: #222225;
    --rule: #d9dde2;
    --blue-light: #1a6aa8;
    --blue-mid: #155a92;
    --blue-dark: #0f3f6e;
    --badge: #2a2a2e;
    --ink: #ffffff;
  }
  html, body {
    margin: 0;
    padding: 0;
    width: 1081px;
    height: 1200px;
    overflow: hidden;
    background: var(--page);
  }
  .canvas {
    position: relative;
    width: 1081px;
    height: 1200px;
  }
  .sign {
    position: absolute;
    left: 40px;
    top: 433px;
    width: 1000px;
    height: 334px;
    background:
      radial-gradient(ellipse at 85% 10%, var(--blue-light) 0%, transparent 55%),
      radial-gradient(ellipse at 20% 90%, var(--blue-dark) 0%, transparent 60%),
      linear-gradient(160deg, var(--blue-mid), var(--blue-dark));
    box-shadow: 0 2px 6px rgba(0,0,0,0.25);
    overflow: hidden;
  }
  .sign-band {
    position: absolute;
    left: 0; top: 0;
    width: 100%;
    height: 51px;
    background: var(--band);
    border-bottom: 3px solid var(--rule);
  }
  .sign-frame {
    position: absolute;
    inset: 0;
  }
  .brand-badge {
    position: absolute;
    left: 43px;
    top: 94px;
    width: 188px;
    height: 188px;
    border-radius: 50%;
    background: var(--badge);
    display: flex;
    align-items: center;
    justify-content: center;
    text-align: center;
    font-family: "Montserrat", sans-serif;
    font-weight: 700;
    font-size: 28px;
    line-height: 1.1;
    color: var(--ink);
  }
  .headline {
    position: absolute;
    left: 256px;
    top: 78px;
    margin: 0;
    font-family: "Montserrat", sans-serif;
    font-weight: 700;
    font-size: 110px;
    line-height: 1;
    letter-spacing: -1px;
    color: var(--ink);
  }
  .tagline {
    position: absolute;
    left: 259px;
    top: 194px;
    margin: 0;
    font-family: "Hind", sans-serif;
    font-weight: 600;
    font-size: 50px;
    line-height: 1;
    letter-spacing: 0.2px;
    color: var(--ink);
  }
  .contact-row {
    position: absolute;
    left: 260px;
    top: 262px;
    display: flex;
    align-items: center;
    gap: 6px;
    font-family: "Poppins", sans-serif;
    font-weight: 400;
    font-size: 17px;
    color: var(--ink);
    white-space: nowrap;
  }
  .contact-item {
    display: flex;
    align-items: center;
    gap: 6px;
    margin-right: 4px;
  }
  .contact-icon {
    width: 17px;
    height: 17px;
    flex: none;
  }
  .social {
    display: flex;
    align-items: center;
    gap: 4px;
    margin-left: 4px;
    padding-left: 10px;
    border-left: 1px solid var(--ink);
    height: 22px;
    font-size: 7px;
  }
  .social-square {
    width: 11px;
    height: 11px;
    background: var(--ink);
    border-radius: 2px;
  }
</style>
</head>
<body>
<main class="canvas">
  <section class="sign" aria-label="Lumora Mists vape shop storefront sign">
    <div class="sign-band"></div>

    <svg class="sign-frame" width="1000" height="334" viewBox="0 0 1000 334" aria-hidden="true">
      <g stroke="#ffffff" stroke-width="1.2" fill="none">
        <line x1="36" y1="14" x2="340" y2="14"/>
        <line x1="36" y1="19" x2="340" y2="19"/>
        <line x1="660" y1="14" x2="966" y2="14"/>
        <line x1="660" y1="19" x2="966" y2="19"/>
        <line x1="22" y1="14" x2="22" y2="318"/>
        <line x1="28" y1="22" x2="28" y2="318"/>
        <line x1="978" y1="14" x2="978" y2="318"/>
        <line x1="972" y1="22" x2="972" y2="318"/>
        <line x1="34" y1="317" x2="340" y2="317"/>
        <line x1="34" y1="322" x2="340" y2="322"/>
        <line x1="660" y1="317" x2="966" y2="317"/>
        <line x1="660" y1="322" x2="966" y2="322"/>
      </g>
    </svg>

    <div class="brand-badge">Lumora<br>Mists</div>

    <h1 class="headline">VAPE SHOP</h1>
    <p class="tagline">STOP SMOKING START VAPING</p>

    <div class="contact-row">
      <span class="contact-item">
        <svg class="contact-icon" viewBox="0 0 24 24" aria-hidden="true">
          <path fill="#ffffff" d="M6.6 10.8a15.1 15.1 0 0 0 6.6 6.6l2.2-2.2c.3-.3.7-.4 1-.2 1.1.4 2.3.6 3.6.6.6 0 1 .4 1 1V20c0 .6-.4 1-1 1A17 17 0 0 1 3 4c0-.6.4-1 1-1h3.5c.6 0 1 .4 1 1 0 1.3.2 2.5.6 3.6.1.3 0 .7-.2 1z"/>
        </svg>
        562-7038
      </span>
      <span class="contact-item">
        <svg class="contact-icon" viewBox="0 0 24 24" aria-hidden="true">
          <circle cx="12" cy="12" r="10" fill="none" stroke="#ffffff" stroke-width="2.4"/>
        </svg>
        394-6150
      </span>
      <span class="contact-item">
        <svg class="contact-icon" viewBox="0 0 24 24" aria-hidden="true">
          <g fill="none" stroke="#ffffff" stroke-width="1.8">
            <circle cx="12" cy="12" r="10"/>
            <ellipse cx="12" cy="12" rx="4.5" ry="10"/>
            <line x1="2" y1="12" x2="22" y2="12"/>
            <path d="M4 7h16M4 17h16"/>
          </g>
        </svg>
        www.lumora-mists.business.site
      </span>
      <span class="social">
        Follow us on
        <span class="social-square"></span>
        <span class="social-square"></span>
      </span>
    </div>
  </section>
</main>
</body>
</html>
```